New Bicycle shop business card

Hi!
I'm looking for a business card for my new proffesional bike mechanics shop. This shop is only for fixing broken bikes and not selling bikes.
Peferbly a modern and sleek and modern design.
Colors: black, grey, red, white
Information:
Name: Rijwielwerkplaats Vanhoutte
Shop owner: Bart Vanhoutte & Marieke Segers
Website: www.rijwielwerkplaats-vanhoutte.be
Email: info@rijwielwerkplaats-vanhoutte.be
Phone number: +32471902368
Street adres: Kerkweg 46
9940 Bellebeke
Slogan/shop information: Herstellingen van alle merken.
Logo: see files.
Target Market(s)
People who seek a mechanic to fix or upgrade their bikes.
Contact Information for Business Card
Information:
Website: info@rijwielwerkplaats-vanhoutte.be
9940 Bellebeke
Logo: see files.

```html
<!DOCTYPE html>
<html lang="nl">
<head>
<meta charset="utf-8">
<title>Rijwielwerkplaats Vanhoutte – visitekaartje</title>
<link rel="stylesheet" href="https://fonts.googleapis.com/css2?family=Lato:wght@400;700;900&display=swap">
<style>
  :root {
    --page: #e9e9ea;
    --card: #1d1e20;
    --card-edge: #161719;
    --red: #e3173e;
    --white: #ffffff;
    --grey: #c9c9cb;
    --line: #6a6b6e;
    --pattern-top: #2a2b2e;
    --pattern-bottom: #1d1e20;
  }
  * { box-sizing: border-box; margin: 0; padding: 0; }
  html, body { width: 1200px; height: 1108px; overflow: hidden; }
  body {
    background: var(--page);
    font-family: "Lato", sans-serif;
    display: flex;
    align-items: center;
    justify-content: center;
    gap: 64px;
  }
  .card {
    width: 400px;
    height: 640px;
    background: var(--card);
    border-radius: 22px;
    color: var(--white);
    position: relative;
    overflow: hidden;
    box-shadow: 0 10px 30px rgba(0,0,0,.18);
  }

  /* front */
  .card-front {
    display: flex;
    flex-direction: column;
    align-items: center;
    text-align: center;
    padding-top: 92px;
  }
  .brand-dot {
    width: 62px; height: 62px;
    border-radius: 50%;
    background: var(--red);
    margin-bottom: 26px;
  }
  .brand-name {
    font-weight: 900;
    font-size: 30px;
    line-height: 1.12;
    letter-spacing: .5px;
    text-transform: uppercase;
    color: var(--white);
  }
  .owners {
    margin-top: 40px;
    font-size: 17px;
    font-weight: 400;
    color: var(--red);
    text-transform: uppercase;
  }
  .role {
    font-size: 15px;
    color: var(--grey);
    margin-top: 2px;
  }
  .icon-rule {
    display: flex;
    align-items: center;
    gap: 8px;
    width: 240px;
    margin: 14px 0 10px;
  }
  .icon-rule .rule { flex: 1; height: 1px; background: var(--line); }
  .icon-rule svg { width: 22px; height: 22px; display: block; }
  .contact {
    font-size: 17px;
    line-height: 1.35;
    color: var(--white);
  }
  .divider {
    width: 240px; height: 1px;
    background: var(--line);
    margin: 12px 0 10px;
  }
  .address {
    font-size: 17px;
    line-height: 1.35;
    color: var(--white);
  }

  /* back */
  .card-back .pattern-field {
    position: absolute;
    inset: 0 0 180px 0;
    background: linear-gradient(180deg, var(--pattern-top), var(--pattern-bottom));
  }
  .back-brand {
    position: absolute;
    left: 40px; right: 40px; bottom: 70px;
    text-align: center;
  }
  .back-brand .brand-name { font-size: 30px; }
  .tagline {
    margin-top: 14px;
    font-size: 17px;
    color: var(--white);
    text-transform: uppercase;
    letter-spacing: .3px;
  }
</style>
</head>
<body>

  <article class="card card-front">
    <span class="brand-dot"></span>
    <h1 class="brand-name">Rijwielwerkplaats<br>Vanhoutte</h1>

    <p class="owners">Bart Vanhoutte &amp; Marieke Segers</p>
    <p class="role">Owner</p>

    <div class="icon-rule">
      <span class="rule"></span>
      <svg viewBox="0 0 24 24" aria-label="Telefoon"><circle cx="12" cy="12" r="12" fill="#e3173e"/><path d="M8.2 6.5l2 2-1.2 1.6c.8 1.7 2.2 3.1 3.9 3.9l1.6-1.2 2 2-1.3 2c-4.4-.4-8.6-4.6-9-9z" fill="#1d1e20"/></svg>
      <svg viewBox="0 0 24 24" aria-label="E-mail"><circle cx="12" cy="12" r="12" fill="#e3173e"/><rect x="6" y="8" width="12" height="8" fill="#1d1e20"/><path d="M6 8l6 4.5L18 8" fill="none" stroke="#e3173e" stroke-width="1.2"/></svg>
      <svg viewBox="0 0 24 24" aria-label="Website"><circle cx="12" cy="12" r="12" fill="#e3173e"/><g fill="none" stroke="#1d1e20" stroke-width="1.4"><circle cx="12" cy="12" r="6"/><ellipse cx="12" cy="12" rx="2.6" ry="6"/><path d="M6 12h12"/></g></svg>
      <span class="rule"></span>
    </div>

    <p class="contact">
      +32471902368<br>
      info@rijwielwerkplaats-vanhoutte.be<br>
      www.rijwielwerkplaats-vanhoutte.be
    </p>
    <span class="divider"></span>
    <p class="address">
      Kerkweg 46<br>
      9940 Bellebeke
    </p>
  </article>

  <article class="card card-back">
    <div class="pattern-field" role="img" aria-label="Faint repeating brand emblem pattern on dark grey"></div>
    <div class="back-brand">
      <h2 class="brand-name">Rijwielwerkplaats<br>Vanhoutte</h2>
      <p class="tagline">Herstellingen van alle merken</p>
    </div>
  </article>

</body>
</html>
```